Ledgers On Track Business Card Design

We are a bookkeeping and accounting practice and are particularly passionate about Vantu as 'state of the art' accounting software. We offer a number of services which are listed on the back of the card. The logos for LOT have already been developed. There are also other logos of organisations we are involved with - Vantu (both certified advisor and silver partner), QAG, and filenow hub. Regarding colours, we would like to use the colours similar to our website, www.ledgersontrack.com, and these connect with the www.vantu.com.au website. The proposed layout as it is just does not look too great - it looks like an amateur has done it - which is true!

Industry/Entity Type

Accounting

Contact Information for Business Card

The details to appear on the card are found on the files uploaded. I have front and back rough layouts.

```html
<!DOCTYPE html>
<html lang="en">
<head>
<meta charset="utf-8">
<title>Ledgers On Track – Business Card</title>
<link rel="stylesheet" href="https://fonts.googleapis.com/css2?family=Tinos:wght@400;700&display=swap">
<style>
  :root {
    --brand-blue: #4a5c9a;
    --brand-green: #4f9a3e;
    --text-dark: #222222;
    --text-grey: #5e5e5e;
    --abn-grey: #a3a3a3;
    --guild-grey: #3c3c3c;
    --icon-green: #4aa33f;
    --accreditation-tint: #dfe3f0;
    --paper: #ffffff;
  }
  * { margin: 0; padding: 0; box-sizing: border-box; }
  html, body { width: 1200px; height: 722px; overflow: hidden; background: var(--paper); }
  .card {
    position: relative;
    width: 1200px;
    height: 722px;
    background: var(--paper);
    font-family: "Tinos", "Times New Roman", serif;
    overflow: hidden;
  }
  .backdrop-motif {
    position: absolute;
    left: 540px;
    top: 80px;
    width: 660px;
    height: 564px;
    background: radial-gradient(closest-side at 55% 70%, rgba(226, 236, 222, 0.8) 0%, rgba(232, 233, 245, 0.55) 50%, rgba(255, 255, 255, 0) 100%);
  }
  .brand-mark {
    position: absolute;
    left: 78px;
    top: 86px;
    width: 84px;
    height: 84px;
    border-radius: 50%;
    background: var(--brand-green);
  }
  .brand-name {
    position: absolute;
    left: 196px;
    top: 76px;
    font-weight: 700;
    font-size: 98px;
    line-height: 1;
    color: var(--brand-blue);
    white-space: nowrap;
  }
  .abn {
    position: absolute;
    left: 110px;
    top: 194px;
    font-size: 20px;
    color: var(--abn-grey);
  }
  .guild {
    position: absolute;
    left: 96px;
    top: 316px;
    font-size: 30px;
    line-height: 1.2;
    color: var(--guild-grey);
    white-space: nowrap;
  }
  .contacts {
    position: absolute;
    left: 106px;
    top: 404px;
    list-style: none;
  }
  .contacts li {
    display: flex;
    align-items: center;
    height: 41px;
    font-size: 29px;
    color: var(--text-dark);
  }
  .contacts svg { width: 26px; height: 26px; margin-right: 20px; flex: none; }
  .person {
    position: absolute;
    left: 650px;
    width: 500px;
    top: 312px;
    text-align: center;
  }
  .person-name { font-size: 52px; font-weight: 700; color: var(--brand-green); line-height: 1.05; }
  .person-role { font-size: 25px; color: var(--text-grey); margin-top: 4px; }
  .accreditation {
    position: absolute;
    left: 770px;
    top: 462px;
    width: 260px;
    height: 96px;
    border-radius: 48px;
    background: var(--accreditation-tint);
  }
  .address-band {
    position: absolute;
    left: 0;
    top: 644px;
    width: 1200px;
    height: 78px;
    background: var(--brand-blue);
    color: var(--paper);
    font-size: 28px;
    display: flex;
    align-items: center;
    justify-content: center;
  }
</style>
</head>
<body>
<main class="card">
  <div class="backdrop-motif" role="img" aria-label="Faint open book motif in soft green and lavender"></div>

  <div class="brand-mark"></div>
  <h1 class="brand-name">Ledgers On Track</h1>
  <p class="abn">ABN 52 617 308 442</p>

  <p class="guild">Queensgate Accounting Guild</p>

  <ul class="contacts">
    <li>
      <svg viewBox="0 0 26 26"><rect width="26" height="26" rx="4" fill="var(--icon-green)"/><path d="M6 10c0-2 3-3 7-3s7 1 7 3v1h-4v-1.5h-6V11H6z M8 12h10l2 7H6z" fill="#fff"/><circle cx="13" cy="15.5" r="2" fill="var(--icon-green)"/></svg>
      03 9012 4471
    </li>
    <li>
      <svg viewBox="0 0 26 26"><rect width="26" height="26" rx="4" fill="var(--icon-green)"/><rect x="8" y="4" width="10" height="18" rx="2" fill="#fff"/><rect x="10" y="7" width="6" height="10" fill="var(--icon-green)"/></svg>
      0412 556 308
    </li>
    <li>
      <svg viewBox="0 0 26 26"><rect width="26" height="26" rx="4" fill="var(--icon-green)"/><rect x="5" y="8" width="16" height="11" fill="#fff"/><path d="M5 8l8 6 8-6" fill="none" stroke="var(--icon-green)" stroke-width="1.5"/></svg>
      hmarsh@ledgersontrack.com
    </li>
    <li>
      <svg viewBox="0 0 26 26"><rect width="26" height="26" rx="4" fill="var(--icon-green)"/><g fill="none" stroke="#fff" stroke-width="1.4"><circle cx="13" cy="13" r="7.5"/><ellipse cx="13" cy="13" rx="3.5" ry="7.5"/><path d="M5.5 13h15M7 9h12M7 17h12"/></g></svg>
      www.ledgersontrack.com
    </li>
  </ul>

  <section class="person">
    <h2 class="person-name">Helen Marsh</h2>
    <p class="person-role">Partner</p>
  </section>

  <div class="accreditation"></div>

  <footer class="address-band">18 Linden Grove Road, Kellbrook VIC 3187</footer>
</main>
</body>
</html>
```